Roofing Company Modern look

I want a modern and sophisticated look for our roofing business.

Our address is :

5217 Mallow Creek Ln
Orlando, Fl 32825

(407)-583-2196

www.HarborlineRoofsFl.com

I also want to make sure on the back there is a spot to put
Project Manager Name :

Number:

Because the cards will be used by all sales people

Project Manager Name :

Also there are accreditation we have logos are uploaded here as well that I would like maybe on the back of card as well

I also want to highlight our special attributions or trades:

Residential & Commercial
Fully Insured
License # CCC7482913
Insurance Claims
Serving Central Florida Since 1992
Free Estimates

Contact Information for Business Card

Our address is :

5217 Mallow Creek Ln
Orlando, Fl 32825

(407)-583-2196

Project Manager Name :

Residential & Commercial
Fully Insured
License # CCC7482913
Insurance Claims
Free Estimates

Font styles to use
Serif
Sans Serif

Colors
3176b5

Requirements
Must have
• Must have royal blue like my logo grey and black are the colors I like

```html
<!DOCTYPE html>
<html lang="en">
<head>
<meta charset="utf-8">
<title>Harborline Roofs &amp; Gutters – Business Card</title>
<link rel="stylesheet" href="https://fonts.googleapis.com/css2?family=Questrial&family=Roboto+Condensed:wght@400&display=swap">
<style>
  :root {
    --royal: #3176b5;
    --royal-deep: #1a5fa6;
    --sky: #4aa3d8;
    --ink: #2b2b2b;
    --grey: #8d8f92;
    --card: #ffffff;
    --backdrop: #e4e4e4;
    --label: #3a7ab8;
  }
  html, body { margin: 0; padding: 0; overflow: hidden; }
  body {
    width: 1200px; height: 1200px;
    background: var(--backdrop);
    position: relative;
    font-family: "Questrial", sans-serif;
  }
  .card-slot {
    position: absolute; left: 257px;
    width: 686px; height: 391px;
  }
  .card-slot.front { top: 165px; }
  .card-slot.back { top: 653px; }
  .card {
    position: absolute; left: 0; top: 0;
    width: 800px; height: 456px;
    transform: scale(0.8575); transform-origin: 0 0;
    background: var(--card);
    border-radius: 26px; overflow: hidden;
    box-shadow: 0 10px 22px rgba(0,0,0,0.18);
  }
  .wave { position: absolute; left: 0; top: 0; width: 800px; height: 456px; }
  .web-tab {
    position: absolute; right: 0; bottom: 0;
    width: 388px; height: 52px;
    background: var(--card);
    border-top-left-radius: 44px;
    display: flex; align-items: center; justify-content: flex-end;
    padding-right: 38px; box-sizing: border-box;
    color: var(--ink); font-size: 22px;
  }
  /* front */
  .brand {
    position: absolute; left: 50px; top: 70px; width: 270px;
    text-align: center; color: var(--royal);
  }
  .brand-dot {
    width: 74px; height: 74px; border-radius: 50%;
    background: var(--royal); margin: 0 auto 14px;
  }
  .brand-name { font-size: 37px; letter-spacing: 3px; line-height: 1; }
  .brand-sub { font-size: 13px; letter-spacing: 2.4px; margin-top: 6px; }
  .address {
    position: absolute; right: 38px; top: 272px;
    text-align: right; color: #fff; font-size: 22px; line-height: 26px;
  }
  .phone {
    position: absolute; right: 36px; top: 334px;
    color: #fff; font-size: 48px; line-height: 1;
  }
  /* back */
  .field {
    position: absolute; left: 61px;
    font-family: "Roboto Condensed", sans-serif;
    font-size: 18px; color: var(--label);
    display: flex; align-items: flex-end;
  }
  .field .rule { border-bottom: 1px solid var(--label); margin-left: 6px; margin-bottom: 4px; }
  .field.manager { top: 46px; }
  .field.manager .rule { width: 474px; }
  .field.phone-line { top: 109px; }
  .field.phone-line .rule { width: 348px; }
  .badge { position: absolute; background: #c9ced6; }
  .badge.one { left: 56px; top: 172px; width: 52px; height: 66px; border-radius: 4px; }
  .badge.two { left: 128px; top: 182px; width: 72px; height: 46px; background: #3c4a5e; border-radius: 3px; }
  .badge.three { left: 224px; top: 178px; width: 60px; height: 60px; border-radius: 50%; background: #b9bec5; }
  .badge.four { left: 62px; top: 260px; width: 156px; height: 44px; background: #c0282d; border: 2px solid #1b2a55; box-sizing: border-box; }
  .credentials {
    position: absolute; right: 36px; top: 224px;
    list-style: none; margin: 0; padding: 0;
    text-align: right; color: #fff;
    font-family: "Roboto Condensed", sans-serif; font-size: 21px; line-height: 25.6px;
  }
  .credentials li::after {
    content: ""; display: inline-block;
    width: 12px; height: 12px; border-radius: 50%;
    background: #fff; margin-left: 9px; vertical-align: 1px;
  }
</style>
</head>
<body>

<svg width="0" height="0" style="position:absolute">
  <defs>
    <linearGradient id="blueFill" x1="0" y1="1" x2="1" y2="0">
      <stop offset="0" stop-color="#1a5fa6"/>
      <stop offset="0.5" stop-color="#2b85c6"/>
      <stop offset="1" stop-color="#4aa8db"/>
    </linearGradient>
    <linearGradient id="greyFill" x1="0" y1="0" x2="1" y2="0">
      <stop offset="0" stop-color="#111"/>
      <stop offset="0.5" stop-color="#555"/>
      <stop offset="1" stop-color="#a8aaad"/>
    </linearGradient>
    <symbol id="swoosh" viewBox="0 0 800 456">
      <path d="M0,350 C120,395 270,392 385,262 C475,160 565,82 685,82 C742,82 780,96 800,106 L800,456 L0,456 Z" fill="url(#greyFill)"/>
      <path d="M0,362 C130,400 285,388 400,272 C490,182 580,100 690,100 C742,100 780,112 800,122 L800,456 L0,456 Z" fill="url(#blueFill)"/>
      <path d="M0,392 C160,428 330,420 470,330 C600,250 700,260 800,300 L800,456 L0,456 Z" fill="#1f68ad" opacity="0.55"/>
    </symbol>
  </defs>
</svg>

<div class="card-slot front">
  <div class="card">
    <svg class="wave" viewBox="0 0 800 456"><use href="#swoosh"/></svg>
    <div class="brand">
      <div class="brand-dot"></div>
      <div class="brand-name">HARBORLINE</div>
      <div class="brand-sub">ROOFS &amp; GUTTERS INC.</div>
    </div>
    <div class="address">5217 Mallow Creek Ln<br>Orlando, Fl 32825</div>
    <div class="phone">(407)-583-2196</div>
    <div class="web-tab">www.HarborlineRoofsFl.com</div>
  </div>
</div>

<div class="card-slot back">
  <div class="card">
    <svg class="wave" viewBox="0 0 800 456"><use href="#swoosh"/></svg>
    <div class="field manager">PROJECT MANAGER NAME :<span class="rule"></span></div>
    <div class="field phone-line">PHONE:<span class="rule"></span></div>
    <div class="badge one" role="img" aria-label="Accreditation badge"></div>
    <div class="badge two" role="img" aria-label="Certified applicator badge"></div>
    <div class="badge three" role="img" aria-label="Screened and approved badge"></div>
    <div class="badge four" role="img" aria-label="Authorized contractor badge"></div>
    <ul class="credentials">
      <li>RESIDENTIAL &amp; COMMERCIAL</li>
      <li>FULLY INSURED</li>
      <li>LICENSE # CCC7482913</li>
      <li>INSURANCE CLAIMS</li>
      <li>SERVING CENTRAL FLORIDA SINCE 1992</li>
      <li>FREE ESTIMATES</li>
    </ul>
    <div class="web-tab">www.HarborlineRoofsFl.com</div>
  </div>
</div>

</body>
</html>
```